Harborline Auto LLC

Car Dealer Customer Service
Address: 2874 Cresthaven Road, Shelbyville, TN 37162
web: www.harborlineautoxq.net
email: harborlineautoxq@mailnest.example
Phone: (931) 555-0148
Phone: (629) 555-0173

```html
<!DOCTYPE html>
<html lang="en">
<head>
<meta charset="utf-8">
<title>Harborline Auto – Business Card</title>
<link rel="stylesheet" href="https://fonts.googleapis.com/css2?family=Montserrat:wght@400;500;800&display=swap">
<style>
  :root {
    --brand-blue: #1f7fb8;
    --band-blue: #2b97d2;
    --brand-yellow: #ecb13f;
    --ink: #1b1b1b;
    --card: #ffffff;
    --backdrop: #e6e7e9;
  }
  * { box-sizing: border-box; margin: 0; padding: 0; }
  html, body { width: 1200px; height: 960px; overflow: hidden; }
  body {
    background: var(--backdrop);
    font-family: "Montserrat", sans-serif;
    color: var(--ink);
  }
  .card {
    position: absolute;
    left: 250px;
    width: 700px;
    height: 400px;
    background: var(--card);
    border-radius: 22px;
    overflow: hidden;
    box-shadow: 0 6px 18px rgba(0,0,0,0.12);
  }
  .card--front { top: 60px; }
  .card--back { top: 500px; }

  .brand {
    position: absolute;
    display: flex;
    flex-direction: column;
    align-items: center;
    gap: 18px;
  }
  .brand__mark {
    width: 86px; height: 86px;
    border-radius: 50%;
    background: var(--band-blue);
  }
  .brand__name {
    font-weight: 800;
    font-size: 40px;
    letter-spacing: 1px;
    color: var(--brand-blue);
    text-transform: uppercase;
    white-space: nowrap;
  }
  .card--front .brand { left: 0; right: 0; top: 120px; }

  .card--back .brand { left: 28px; width: 320px; top: 90px; gap: 14px; }
  .card--back .brand__mark { width: 70px; height: 70px; }
  .card--back .brand__name { font-size: 29px; }

  .divider {
    position: absolute;
    left: 370px; top: 70px;
    width: 1.5px; height: 170px;
    background: var(--band-blue);
  }
  .contact {
    position: absolute;
    left: 392px; top: 58px;
    font-size: 14.5px;
    line-height: 1.32;
  }
  .contact__role { font-size: 15px; margin-bottom: 8px; }
  .contact__address { margin-bottom: 10px; }
  .contact__list { list-style: none; }
  .contact__list li { display: flex; align-items: center; gap: 8px; margin-bottom: 3px; }
  .contact__list svg { width: 13px; height: 13px; flex: none; fill: var(--band-blue); }
  .contact__web-domain { color: var(--band-blue); }

  .bands { position: absolute; left: 0; bottom: 0; width: 700px; height: 110px; }
</style>
</head>
<body>
  <section class="card card--front">
    <div class="brand">
      <div class="brand__mark"></div>
      <div class="brand__name">Harborline Auto</div>
    </div>
  </section>

  <section class="card card--back">
    <div class="brand">
      <div class="brand__mark"></div>
      <div class="brand__name">Harborline Auto</div>
    </div>

    <div class="divider"></div>

    <div class="contact">
      <p class="contact__role">Car Dealer Customer Service</p>
      <p class="contact__address">2874 Cresthaven Road,<br>Shelbyville, TN 37162</p>
      <ul class="contact__list">
        <li>
          <svg viewBox="0 0 16 16"><path d="M3 1l3 3-1.5 2a9 9 0 0 0 5.5 5.5L12 10l3 3-2 2C7 15 1 9 1 3z"/></svg>
          (931) 555-0148
        </li>
        <li>
          <svg viewBox="0 0 16 16"><path d="M1 5c0-2 14-2 14 0v2h-4V5H5v2H1zM3 8h10l1 6H2z"/></svg>
          (629) 555-0173
        </li>
        <li>
          <svg viewBox="0 0 16 16"><path d="M1 3h14v10H1zM2 4l6 5 6-5v1L8 10 2 5z" fill-rule="evenodd"/></svg>
          harborlineautoxq@mailnest.example
        </li>
        <li>
          <svg viewBox="0 0 16 16"><circle cx="8" cy="8" r="7"/></svg>
          www.<span class="contact__web-domain">harborlineautoxq</span>.net
        </li>
      </ul>
    </div>

    <svg class="bands" viewBox="0 0 700 110" preserveAspectRatio="none">
      <polygon points="0,94 440,50 425,110 0,110" fill="var(--brand-yellow)"/>
      <polygon points="450,49 700,24 700,110 435,110" fill="var(--band-blue)"/>
    </svg>
  </section>
</body>
</html>
```